Financial Services Consultant needs a business card

We need a business card for a new consulting company based in Melbourne called
"Quelbrook Insights". Tagline is Track, Review, Grow
We would like to see business card designs that are in line with the minimal style of the website www.quelbrook-insights.example
The font I have used on the website is Proxima Nova and would like the same or similar font used on the business card with a minimal design in line with the website Two sided with "QUELBROOK INSIGHTS" TRACK, REVIEW, GROW on one side and name, title and contact details on the otther
Updates

Hi All, thanks for your submissions, much appreciated.

I have recently added some colour to my webiste, it is hex #3a7b74 for those that wish to use it
Thanks

Hi all

thanks very much for your design submissions I am very impressed and they are much appreciated.

Interms of general feedback please find below;

Colour: I am trying to stick to a minimal design and colour scheme for my website which is still under construction, up to 3 colours( www.quelbrook-insights.example) it is currently black and white with a small amount of blue/green but I am open to suggestion/interpretations for a consulting company.

Card: I dont mind if it has rounded edges or straight, I was thinking about using a letterpress card if possible

Detail: the detail on the card will include; Name, Title, Mobile, Personal Email, Business Email,Web,Business Address

Once again thanks for submissions

Industry/Entity Type

Business

```html
<!DOCTYPE html>
<html lang="en">
<head>
<meta charset="utf-8">
<title>Quelbrook Insights – Business Card</title>
<link href="https://fonts.googleapis.com/css2?family=Montserrat:wght@400;500;600;700&display=swap" rel="stylesheet">
<style>
  :root {
    --ink: #111111;
    --paper: #ffffff;
    --teal: #3a7b74;
    --grey: #555555;
    --rule: #b8b8b8;
    --backdrop: #e9e9e7;
  }
  * { box-sizing: border-box; margin: 0; padding: 0; }
  html, body {
    width: 1200px; height: 720px; overflow: hidden;
    background: var(--backdrop);
    font-family: "Montserrat", Arial, sans-serif;
    color: var(--ink);
  }
  .sheet {
    width: 1200px; height: 720px;
    display: flex; align-items: center; justify-content: center; gap: 40px;
  }
  .card {
    position: relative;
    width: 540px; height: 310px;
    background: var(--paper);
    box-shadow: 0 6px 18px rgba(0,0,0,.12);
    overflow: hidden;
  }
  .wordmark {
    font-weight: 700;
    letter-spacing: .12em;
    color: var(--ink);
    white-space: nowrap;
  }

  /* contact side */
  .card--contact .wordmark {
    position: absolute; top: 46px; left: 0; right: 0;
    text-align: center; font-size: 28px;
  }
  .person {
    position: absolute; top: 114px; left: 0; right: 0;
    text-align: center; font-size: 16px; font-weight: 600;
  }
  .person .title { color: var(--teal); font-weight: 500; }
  .details {
    position: absolute; top: 148px; left: 0; right: 0;
    display: flex; justify-content: center; gap: 14px;
    font-size: 11.5px; color: var(--grey); line-height: 1.6;
  }
  .details .address { text-align: right; padding-top: 16px; }
  .details .divider { width: 1px; background: var(--rule); }
  .details .contact-line { display: flex; align-items: center; gap: 6px; }
  .details svg { width: 11px; height: 11px; flex: none; }
  .rule-teal {
    position: absolute; left: 0; right: 0; bottom: 50px;
    height: 2px; background: var(--teal);
  }
  .tagline-band {
    position: absolute; left: 0; right: 0; bottom: 0; height: 46px;
    background: var(--ink); color: var(--paper);
    display: flex; align-items: center; justify-content: center;
    font-size: 15px; font-weight: 500; letter-spacing: .02em;
  }

  /* brand side */
  .card--brand { display: flex; flex-direction: column; align-items: center; justify-content: center; }
  .brand-lockup { display: flex; align-items: baseline; gap: 4px; }
  .card--brand .wordmark { font-size: 26px; }
  .brand-lockup .suffix { font-size: 11px; color: var(--grey); letter-spacing: .12em; }
  .web {
    margin-top: 24px; font-size: 13px; letter-spacing: .2em; color: var(--grey);
  }
  .web b { color: var(--ink); font-weight: 700; }
</style>
</head>
<body>
<main class="sheet">
  <section class="card card--contact" aria-label="Card front with contact details">
    <div class="wordmark">QUELBROOK INSIGHTS</div>
    <p class="person">Your Name, <span class="title">Title</span></p>
    <div class="details">
      <div class="address">Street Name, City Name<br>State Zip Code</div>
      <div class="divider"></div>
      <div class="contact-list">
        <div class="contact-line">
          <svg viewBox="0 0 12 12" aria-hidden="true"><circle cx="6" cy="6" r="5.4" fill="none" stroke="#555" stroke-width="1"/><path d="M4 3.2l1 1.3-.6.7c.4.9 1.1 1.6 2 2l.7-.6 1.3 1-.6 1c-2.4-.2-4.3-2.1-4.5-4.5z" fill="#555"/></svg>
          <span>123-555-0147</span>
        </div>
        <div class="contact-line">
          <svg viewBox="0 0 12 12" aria-hidden="true"><circle cx="6" cy="6" r="5.4" fill="#555"/><path d="M6 .8v10.4M.8 6h10.4M6 .8c-2 2.8-2 7.6 0 10.4M6 .8c2 2.8 2 7.6 0 10.4" stroke="#fff" stroke-width=".7" fill="none"/></svg>
          <span>www.quelbrook-insights.example</span>
        </div>
      </div>
    </div>
    <div class="rule-teal"></div>
    <div class="tagline-band">Track, Review, Grow</div>
  </section>

  <section class="card card--brand" aria-label="Card back with brand name">
    <div class="brand-lockup">
      <span class="wordmark">QUELBROOK INSIGHTS</span><span class="suffix">.example</span>
    </div>
    <p class="web">www.<b>quelbrook-insights</b>.example</p>
  </section>
</main>
</body>
</html>
```